Business Card for a Dental Office

The design should communicate integrity, quality and reliability. We also want the card look elegant, simple, but still stand out, different from the traditional-dental-office business card.

Industry/Entity Type

Business

```html
<!DOCTYPE html>
<html lang="en">
<head>
<meta charset="utf-8">
<title>Harlow Dental Studio – Business Card</title>
<link rel="stylesheet" href="https://fonts.googleapis.com/css2?family=Oswald:wght@500&family=Questrial&display=swap">
<style>
  :root {
    --backdrop: #1c1c1d;
    --card: #121213;
    --card-edge: #1f1f21;
    --emboss: #2c2c2e;
    --emboss-light: #3a3a3c;
    --gold: #d8b41e;
    --ink: #eeeeee;
    --ink-soft: #cfcfcf;
  }
  * { box-sizing: border-box; margin: 0; padding: 0; }
  html, body {
    width: 1200px; height: 786px; overflow: hidden;
    background: var(--backdrop);
  }
  .canvas {
    position: relative; width: 1200px; height: 786px;
    display: flex; align-items: center; justify-content: center; gap: 40px;
  }
  .card {
    position: relative; width: 540px; height: 309px;
    background: var(--card);
    border: 1px solid var(--card-edge);
    border-radius: 3px;
    box-shadow: 0 18px 40px rgba(0,0,0,.55);
    font-family: "Questrial", sans-serif;
    color: var(--ink);
  }
  /* brand lockup */
  .brand {
    position: absolute; display: flex; align-items: flex-end; gap: 10px;
  }
  .brand-mark { width: 30px; height: 30px; flex: none; }
  .brand-name {
    font-family: "Oswald", sans-serif; font-weight: 500;
    font-size: 30px; line-height: 1; letter-spacing: .5px;
    text-transform: uppercase; white-space: nowrap;
  }
  .brand-tagline {
    font-family: "Oswald", sans-serif; font-weight: 500;
    font-size: 13px; letter-spacing: 1.6px; text-transform: uppercase;
    position: absolute; white-space: nowrap;
  }
  /* back side */
  .card-back .brand { left: 78px; top: 110px; }
  .card-back .brand-mark { background: var(--emboss); }
  .card-back .brand-name { color: var(--emboss-light); }
  .card-back .brand-tagline { left: 118px; top: 152px; color: var(--emboss); }
  /* front side */
  .card-front .brand { left: 150px; top: 48px; }
  .card-front .brand-mark { background: var(--gold); }
  .card-front .brand-name { color: var(--ink); }
  .card-front .brand-tagline { left: 190px; top: 90px; color: var(--gold); }

  .address {
    position: absolute; left: 36px; top: 170px;
    font-size: 14px; line-height: 1.45; color: var(--ink-soft);
  }
  .contacts {
    position: absolute; left: 182px; top: 172px;
    list-style: none; font-size: 14px; color: var(--ink-soft);
  }
  .contacts li { display: flex; align-items: center; gap: 9px; height: 21px; }
  .contact-icon {
    width: 15px; height: 15px; background: var(--gold); border-radius: 2px;
    display: flex; align-items: center; justify-content: center; flex: none;
  }
  .contact-icon svg { width: 11px; height: 11px; }
  .person {
    position: absolute; right: 34px; bottom: 34px; text-align: right;
  }
  .person-name {
    font-family: "Oswald", sans-serif; font-weight: 500;
    font-size: 21px; letter-spacing: 1.5px; color: var(--gold);
    text-transform: uppercase;
  }
  .person-role { font-size: 15px; color: var(--ink-soft); margin-top: 2px; }
</style>
</head>
<body>
<main class="canvas">

  <section class="card card-back" aria-label="Card back">
    <div class="brand">
      <span class="brand-mark"></span>
      <span class="brand-name">Harlow Dental Studio</span>
    </div>
    <p class="brand-tagline">Your smile is your gift to others</p>
  </section>

  <section class="card card-front" aria-label="Card front">
    <div class="brand">
      <span class="brand-mark"></span>
      <span class="brand-name">Harlow Dental Studio</span>
    </div>
    <p class="brand-tagline">Your smile is your gift to others</p>

    <address class="address" style="font-style:normal">
      215 Alder Lane<br>Westbrook<br>GA 30512
    </address>

    <ul class="contacts">
      <li>
        <span class="contact-icon">
          <svg viewBox="0 0 12 12"><path d="M3 1.2 4.6 3.4 3.7 4.5c.7 1.5 1.9 2.7 3.4 3.4l1.1-.9 2.2 1.6-.9 2c-4.4-.3-8-3.9-8.3-8.3z" fill="#121213"/></svg>
        </span>(555) 014-2290
      </li>
      <li>
        <span class="contact-icon">
          <svg viewBox="0 0 12 12"><rect x="1" y="2.5" width="10" height="7" fill="none" stroke="#121213" stroke-width="1.2"/><path d="M1 2.5 6 6.5 11 2.5" fill="none" stroke="#121213" stroke-width="1.2"/></svg>
        </span>hello@harlowdental.com
      </li>
      <li>
        <span class="contact-icon">
          <svg viewBox="0 0 12 12"><g fill="none" stroke="#121213" stroke-width="1"><circle cx="6" cy="6" r="4.8"/><ellipse cx="6" cy="6" rx="2" ry="4.8"/><path d="M1.2 6h9.6M2 3.6h8M2 8.4h8"/></g></svg>
        </span>www.harlowdental.com
      </li>
    </ul>

    <div class="person">
      <p class="person-name">Morgan Ellis</p>
      <p class="person-role">General Manager</p>
    </div>
  </section>

</main>
</body>
</html>
```